Bluecrest Learning Corps by graduating students from college in two years

Based on the logo design, create stationary and business cards for
Dr. Venrel T Oskamp, CEO, (703) 482-1736
and Marisa Deltoft, Respresentative, (301) 647-2208
Address: 4719 Pellham Court, Halvern Station, VA 22187
Incorporate elelments of the logo

Target Market(s)

USA

Font styles to use
Other font styles liked:
• match with the logo type style

```html
<!DOCTYPE html>
<html lang="en">
<head>
<meta charset="utf-8">
<title>Bluecrest Learning Corps – Stationery</title>
<link href="https://fonts.googleapis.com/css2?family=Tinos:wght@400;700&display=swap" rel="stylesheet">
<style>
:root{
  --navy:#1f2857;
  --gold:#f8c42f;
  --paper:#fbfbfb;
  --backdrop:#d4dadd;
  --pattern:#f1f2f3;
}
*{box-sizing:border-box;margin:0;padding:0}
html,body{width:1200px;height:916px;overflow:hidden}
body{background:var(--backdrop);font-family:"Tinos","Times New Roman",serif;position:relative;color:var(--navy)}
.card{position:absolute;left:68px;width:438px;height:249px;border-radius:27px;overflow:hidden;background:var(--navy)}
.card--cover{top:66px}
.card--ceo{top:339px}
.card--rep{top:614px}
.card__band{position:absolute;left:0;right:0;top:124px;bottom:0;background:var(--gold)}
.card__marker{position:absolute;left:0;top:26px;width:12px;height:33px;background:var(--gold)}
.card__name{position:absolute;left:16px;top:26px;font-weight:700;font-size:18.5px;color:var(--gold);letter-spacing:.3px;line-height:1}
.card__title{position:absolute;left:16px;top:47px;font-size:11px;color:#fff;line-height:1}
.card__address{position:absolute;left:16px;top:142px;font-size:11px;line-height:15px;color:var(--navy)}
.card__contacts{position:absolute;left:16px;top:183px;list-style:none;font-size:11px;line-height:15px}
.card__contacts li{display:flex;align-items:center;gap:6px}
.card__contacts svg{width:10px;height:10px;fill:var(--navy)}
.seal{position:absolute;border-radius:50%;display:flex;align-items:center;justify-content:center;text-align:center;font-weight:700;color:var(--navy);line-height:1.15}
.seal--cover{left:147px;top:52px;width:144px;height:144px;background:#fff;font-size:15px}
.seal--card{left:258px;top:47px;width:160px;height:160px;background:#fff;font-size:16px}
.letterhead{position:absolute;left:563px;top:66px;width:558px;height:787px;background:var(--paper);overflow:hidden}
.letterhead__pattern{position:absolute;inset:0;background:linear-gradient(160deg,var(--paper),var(--pattern))}
.seal--letter{left:28px;top:29px;width:82px;height:82px;background:var(--navy);color:#fff;font-size:9.5px}
.letterhead__contacts{position:absolute;right:36px;top:27px;list-style:none;text-align:right;font-size:11px;line-height:15px}
.letterhead__contacts li{display:flex;justify-content:flex-end;align-items:flex-start;gap:8px}
.letterhead__contacts li.gap{margin-top:3px}
.letterhead__contacts svg{width:10px;height:10px;fill:var(--gold);margin-top:2px}
.letterhead__rule{position:absolute;left:28px;top:113px;width:376px;height:1px;background:var(--navy)}
.letterhead__rule--accent{left:404px;top:112px;width:124px;height:3px;background:var(--gold)}
</style>
</head>
<body>

<section class="card card--cover">
  <div class="seal seal--cover">Bluecrest<br>Learning<br>Corps</div>
</section>

<section class="card card--ceo">
  <div class="card__band"></div>
  <span class="card__marker"></span>
  <h1 class="card__name">Dr. Venrel T Oskamp</h1>
  <p class="card__title">CEO</p>
  <p class="card__address">4719 Pellham Court,<br>Halvern Station, VA 22187</p>
  <ul class="card__contacts">
    <li><svg viewBox="0 0 10 10"><path d="M2 0l2 2-1 1.5c.6 1.4 1.6 2.4 3 3L7.5 5.5l2 2L8 9.5C4 9 1 6 .5 2z"/></svg>(703) 482-1736</li>
    <li><svg viewBox="0 0 10 10"><circle cx="5" cy="5" r="4.5"/></svg>www.bluecrestlearning.org</li>
    <li><svg viewBox="0 0 10 10"><path d="M0 3l5 3 5-3v6H0zM0 2h10L5 5z"/></svg>info@bluecrestlearning.org</li>
  </ul>
  <div class="seal seal--card">Bluecrest<br>Learning<br>Corps</div>
</section>

<section class="card card--rep">
  <div class="card__band"></div>
  <span class="card__marker"></span>
  <h1 class="card__name">Marisa Deltoft</h1>
  <p class="card__title">Respresentative</p>
  <p class="card__address">4719 Pellham Court,<br>Halvern Station, VA 22187</p>
  <ul class="card__contacts">
    <li><svg viewBox="0 0 10 10"><path d="M2 0l2 2-1 1.5c.6 1.4 1.6 2.4 3 3L7.5 5.5l2 2L8 9.5C4 9 1 6 .5 2z"/></svg>(301) 647-2208</li>
    <li><svg viewBox="0 0 10 10"><circle cx="5" cy="5" r="4.5"/></svg>www.bluecrestlearning.org</li>
    <li><svg viewBox="0 0 10 10"><path d="M0 3l5 3 5-3v6H0zM0 2h10L5 5z"/></svg>info@bluecrestlearning.org</li>
  </ul>
  <div class="seal seal--card">Bluecrest<br>Learning<br>Corps</div>
</section>

<section class="letterhead">
  <div class="letterhead__pattern" role="img" aria-label="Faint repeating graduation cap pattern across the sheet"></div>
  <div class="seal seal--letter">Bluecrest<br>Learning<br>Corps</div>
  <ul class="letterhead__contacts">
    <li><span>4719 Pellham Court,<br>Halvern Station, VA 22187</span><svg viewBox="0 0 10 10"><path d="M5 0a3.5 3.5 0 0 1 3.5 3.5C8.5 6 5 10 5 10S1.5 6 1.5 3.5A3.5 3.5 0 0 1 5 0z"/></svg></li>
    <li class="gap">(301) 647-2208<svg viewBox="0 0 10 10"><path d="M2 0l2 2-1 1.5c.6 1.4 1.6 2.4 3 3L7.5 5.5l2 2L8 9.5C4 9 1 6 .5 2z"/></svg></li>
    <li>www.bluecrestlearning.org<svg viewBox="0 0 10 10"><circle cx="5" cy="5" r="4.5"/></svg></li>
    <li>info@bluecrestlearning.org<svg viewBox="0 0 10 10"><path d="M0 3l5 3 5-3v6H0zM0 2h10L5 5z"/></svg></li>
  </ul>
  <div class="letterhead__rule"></div>
  <div class="letterhead__rule letterhead__rule--accent"></div>
</section>

</body>
</html>
```